Brightfield Ventures Inc. Letterhead

Creation of attractive and eye catching letterhead for a business start-up for the construction industry. Letterhead must relate to construction, but avoid standard hammer and tools in the design.

I forgot to add some details, sorry about that. Some pertinent info: Ph: 916-555-0187 brightfieldventures.example 448 Willowmere Ave, Ste 210 Folsom, CA 95999 info@brightfieldventures.example not sure if slogan should be in there" “Connecting construction professionals to create a purpose driven industry.” must be able to be used in word. Thanks!

```html
<!DOCTYPE html>
<html lang="en">
<head>
<meta charset="utf-8">
<title>Brightfield Ventures Inc. Letterhead</title>
<link href="https://fonts.googleapis.com/css2?family=Arimo:wght@400;700&family=Source+Sans+3:wght@400;600&display=swap" rel="stylesheet">
<style>
  :root {
    --brand-red: #c0121b;
    --brand-navy: #1c2a5e;
    --ink: #3a3a3a;
    --ink-dark: #111;
    --rule: #8a90a8;
    --stage: #e4e5e7;
    --paper: #ffffff;
  }
  * { box-sizing: border-box; margin: 0; padding: 0; }
  html, body {
    width: 1200px; height: 945px; overflow: hidden;
    background: var(--stage);
  }
  .letterhead {
    position: absolute; left: 280px; top: 18px;
    width: 640px; height: 905px;
    background: var(--paper);
    box-shadow: 0 4px 18px rgba(0,0,0,.12);
    overflow: hidden;
    font-family: "Source Sans 3", sans-serif;
    color: var(--ink);
  }
  .header-band { position: absolute; left: 0; top: 0; width: 640px; height: 130px; }
  .brand {
    position: absolute; top: 118px; left: 0; right: 0;
    display: flex; align-items: center; justify-content: center; gap: 8px;
  }
  .brand-block { width: 14px; height: 14px; background: var(--brand-red); }
  .brand-name {
    font-weight: 600; font-size: 17px; letter-spacing: 1.5px;
    color: var(--brand-navy); text-transform: uppercase;
  }
  .brand-rule {
    position: absolute; top: 145px; left: 228px; width: 184px; height: 1px;
    background: var(--brand-red);
  }
  .letter-body {
    position: absolute; top: 200px; left: 78px; width: 500px;
    font-size: 12.5px; line-height: 1.38;
  }
  .salutation {
    font-family: "Arimo", sans-serif; font-weight: 700; font-size: 14px;
    color: var(--ink-dark); margin-bottom: 10px;
  }
  .letter-body p.para { margin-bottom: 14px; }
  .letter-body p.indent { text-indent: 42px; }
  .sign-off {
    position: absolute; top: 648px; left: 110px;
    font-family: "Arimo", sans-serif; font-size: 14px; color: var(--ink-dark);
  }
  .signature {
    width: 110px; height: 34px; margin: 6px 0 6px 20px;
    background: linear-gradient(90deg, rgba(30,30,30,.16), rgba(30,30,30,.04));
    border-radius: 4px;
  }
  .signer { font-weight: 700; font-size: 13px; }
  .footer-rule {
    position: absolute; left: 60px; right: 30px; top: 828px; height: 1px;
    background: linear-gradient(90deg, rgba(138,144,168,.2), var(--rule), rgba(138,144,168,.2));
  }
  .footer-contact {
    position: absolute; right: 40px; top: 838px; text-align: right;
    font-size: 10.5px; line-height: 1.5; color: var(--ink); font-style: normal;
  }
  .footer-contact b { color: var(--brand-red); font-weight: 600; }
  .pin { display: inline-block; vertical-align: -2px; margin-right: 3px; }
  .footer-band {
    position: absolute; left: 0; bottom: 0; width: 640px; height: 20px;
    background: var(--brand-red);
  }
</style>
</head>
<body>
<main class="letterhead">
  <svg class="header-band" viewBox="0 0 640 130" aria-hidden="true">
    <path d="M0 0 H640 V22 Q330 30 0 98 Z" fill="var(--brand-red)"/>
    <path d="M40 116 Q300 42 610 34 Q300 52 40 116 Z" fill="var(--brand-navy)"/>
  </svg>

  <div class="brand">
    <span class="brand-block"></span>
    <span class="brand-name">Brightfield Ventures Inc.</span>
  </div>
  <div class="brand-rule"></div>

  <section class="letter-body">
    <p class="salutation">Dear Mr. Avery,</p>
    <p class="para">Lorem Ipsum is simply dummy text of the printing and typesetting industry. Lorem Ipsum has been the industry's standard dummy text ever since the 1500s, when an unknown printer took a galley of type and scrambled it to make a type specimen book. It has survived not only five centuries, but also the leap into electronic typesetting, remaining essentially unchanged.</p>
    <p class="para indent">The standard chunk of Lorem Ipsum used since the 1500s is reproduced below for those interested. Sections 1.10.32 and 1.10.33 from "de Finibus Bonorum et Malorum" by Cicero are also reproduced in their exact original form, accompanied by English versions from the 1914 translation by H. Rackham</p>
    <p class="para indent">Lorem Ipsum is simply dummy text of the printing and typesetting industry. Lorem Ipsum has been the industry's standard dummy text ever since the 1500s, when an unknown printer took a galley of type and scrambled it to make a type specimen book. It has survived not only five centuries, but also the leap into electronic typesetting, remaining essentially unchanged. It was popularised in the</p>
    <p class="para indent">The standard chunk of Lorem Ipsum used since the 1500s is reproduced below for those interested. Sections 1.10.32 and 1.10.33 from "de Finibus Bonorum et Malorum" by Cicero are also reproduced in their exact original form, accompanied by English versions from the 1914 translation by H. Rackham</p>
    <p class="para indent">The standard chunk of Lorem Ipsum used since the 1500s is reproduced below for those interested. Sections 1.10.32 and 1.10.33 from "de Finibus Bonorum et Malorum" by Cicero</p>
  </section>

  <div class="sign-off">
    <p>Lorem Ipsum</p>
    <div class="signature" role="img" aria-label="Handwritten signature"></div>
    <p class="signer">Lorem Ipsum Admin</p>
  </div>

  <div class="footer-rule"></div>
  <address class="footer-contact">
    <p><svg class="pin" width="8" height="11" viewBox="0 0 8 11" aria-hidden="true"><path d="M4 0 A4 4 0 0 1 8 4 C8 7 4 11 4 11 C4 11 0 7 0 4 A4 4 0 0 1 4 0 Z" fill="var(--brand-red)"/><circle cx="4" cy="4" r="1.5" fill="#fff"/></svg>448 Willowmere Ave, Ste 210, Folsom, CA 95999</p>
    <p><b>P.:</b> 916-555-0187 &nbsp;|&nbsp; <b>E.:</b> info@brightfieldventures.example &nbsp;|&nbsp; <b>W.:</b> brightfieldventures.example</p>
  </address>
  <div class="footer-band"></div>
</main>
</body>
</html>
```